Dynamic Business Card for Sports Supplements Company

Hi! I'm looking for an awesome business card to match my existing sports supplement company. I have uploaded my current company logo and screenshot of the front page of my website.

I would like to have something dynamic and interesting and utilize the colors in the website - the reds and purples

The business card should be double sided and focus on a unique eye-catching design on the back and include all the relevant company info.

Most importantly, it should say somewhere: "Sign up on our website for a coupon code."

Target Market(s)

Mostly for women gym goers but it shouldn't be too feminine. It should be in keeping with the website design. It should flow and clearly be connected to it

Industry/Entity Type

Business

Contact Information for Business Card

Lorraine K. Vestal
CEO
LVestal@Quorvanexco.com
www.quorvanexco.com
555.417.3820
P.O. Box 47315
Fernwick, Ohio 00000

Sign up on our website for a coupon code

Font styles to use
Serif
Sans Serif
Other font styles liked:
• Novecento font family and "Quorvanex" is in AR Destine font

Requirements
Must have
• One side should be a bold Quorvanex logo design. Even just the symbol itself may be o.k. (see attached file)

```html
<!DOCTYPE html>
<html lang="en">
<head>
<meta charset="utf-8">
<title>Quorvanex Business Card</title>
<link href="https://fonts.googleapis.com/css2?family=Saira:wght@400;500;700;800&display=swap" rel="stylesheet">
<style>
  :root {
    --stage: #d9d9d9;
    --card-white: #ffffff;
    --brand-red: #e3232b;
    --ink: #3a3a3a;
    --ink-soft: #555555;
    --card-dark: #262626;
    --band-dark: #1d1d1d;
    --pattern-light: #4a4a4a;
    --pattern-deep: #141414;
    --white: #ffffff;
  }
  * { box-sizing: border-box; margin: 0; padding: 0; }
  html, body {
    width: 1200px; height: 1000px; overflow: hidden;
    background: var(--stage);
    font-family: "Saira", "Helvetica Neue", Arial, sans-serif;
  }
  .stage {
    width: 1200px; height: 1000px;
    display: flex; flex-direction: column; align-items: center; justify-content: center;
    gap: 60px;
  }
  .card {
    position: relative; width: 700px; height: 400px; overflow: hidden;
    box-shadow: 0 6px 18px rgba(0,0,0,.18);
  }

  /* Front side */
  .card-front { background: var(--card-white); }
  .holder { position: absolute; left: 44px; top: 40px; }
  .holder-name {
    color: var(--brand-red); font-weight: 700; font-size: 24px;
    letter-spacing: .04em; text-transform: uppercase; line-height: 1;
  }
  .holder-title { color: var(--ink-soft); font-size: 14px; margin-top: 4px; }
  .contact-list {
    position: absolute; left: 44px; top: 210px; list-style: none;
    color: var(--ink); font-size: 17px; line-height: 1.45;
  }
  .contact-list li { display: flex; align-items: center; gap: 10px; }
  .contact-list svg { width: 16px; height: 16px; fill: var(--brand-red); flex: none; }
  .contact-list .address { margin-top: 2px; }
  .accent { color: var(--brand-red); }
  .front-brand { position: absolute; left: 440px; top: 272px; }
  .brand-name {
    color: var(--brand-red); font-weight: 800; font-size: 34px;
    letter-spacing: .03em; text-transform: uppercase; line-height: 1;
  }
  .brand-tagline {
    color: var(--brand-red); font-size: 13px; letter-spacing: .08em; margin-top: 2px;
  }
  .coupon-band {
    position: absolute; left: 0; bottom: 0; width: 100%; height: 44px;
    background: var(--brand-red); color: var(--white);
    font-size: 18px; letter-spacing: .05em; font-weight: 500;
    display: flex; align-items: center; padding-left: 44px;
  }

  /* Back side */
  .card-back { background: var(--card-dark); }
  .pattern-field {
    position: absolute; left: 0; width: 100%; height: 140px;
    background: linear-gradient(115deg, var(--pattern-deep) 0%, var(--pattern-light) 45%, var(--pattern-deep) 100%);
  }
  .pattern-field.top { top: 0; }
  .pattern-field.bottom { bottom: 0; }
  .brand-band {
    position: absolute; left: 0; top: 140px; width: 100%; height: 120px;
    background: var(--band-dark);
    display: flex; align-items: center; justify-content: center; gap: 16px;
  }
  .brand-square { width: 42px; height: 42px; background: var(--brand-red); flex: none; }
  .back-brand .brand-name { color: var(--white); font-size: 44px; }
  .back-brand .brand-tagline { color: var(--white); font-size: 17px; }
</style>
</head>
<body>
<main class="stage">

  <section class="card card-front" aria-label="Business card front">
    <div class="holder">
      <h1 class="holder-name">Lorraine K. Vestal</h1>
      <p class="holder-title">CEO</p>
    </div>

    <ul class="contact-list">
      <li>
        <svg viewBox="0 0 16 16" aria-hidden="true"><path d="M1 5c0-2 3-3 7-3s7 1 7 3v1h-4V5H5v1H1zM4 7h8l2 7H2z"/></svg>
        555.417.3820
      </li>
      <li>
        <svg viewBox="0 0 16 16" aria-hidden="true"><path d="M1 3h14v10H1zM2 4l6 5 6-5z" fill-rule="evenodd"/></svg>
        LVestal@Quorvanexco.com
      </li>
      <li>
        <svg viewBox="0 0 16 16" aria-hidden="true"><path d="M6.5 1a5.5 5.5 0 014.4 8.8l4 4-1.4 1.4-4-4A5.5 5.5 0 116.5 1zm0 2a3.5 3.5 0 100 7 3.5 3.5 0 000-7z"/></svg>
        <span>www.<span class="accent">quorvanexco</span>.com</span>
      </li>
      <li class="address">P.O. Box 47315 Fernwick, Ohio 00000</li>
    </ul>

    <div class="front-brand">
      <p class="brand-name">Quorvanex</p>
      <p class="brand-tagline">your strength companion</p>
    </div>

    <div class="coupon-band">Sign up on our website for a coupon code</div>
  </section>

  <section class="card card-back" aria-label="Business card back">
    <div class="pattern-field top" role="img" aria-label="Repeating brand symbol pattern in dark and silver tones"></div>
    <div class="brand-band">
      <span class="brand-square" aria-hidden="true"></span>
      <div class="back-brand">
        <p class="brand-name">Quorvanex</p>
        <p class="brand-tagline">your strength companion</p>
      </div>
    </div>
    <div class="pattern-field bottom" role="img" aria-label="Repeating brand symbol pattern in dark and silver tones"></div>
  </section>

</main>
</body>
</html>
```